Business Card Design for Occupational Medicine Start Up Company

We need to design a professional business card. We are a healthcare company providing occupational medicine services to blue collar industries. We are professional, efficient and high quality service providers.

Target Market(s)

Blue Collar Industry: Shipbuilding, Ports, Trucking Companies; The Executives and Safety Officers for these companies

Industry/Entity Type

Healthcare

Contact Information for Business Card

Logo, Name, Title, Email, Phone

Other font styles liked:
• Please match our Brand Guide

Requirements
Must have
• Our Company Colors and Logo

```html
<!DOCTYPE html>
<html lang="en">
<head>
<meta charset="utf-8">
<title>Crewline Health — Business Card</title>
<link rel="stylesheet" href="https://fonts.googleapis.com/css2?family=Montserrat:wght@400;500;700;800&display=swap">
<style>
  :root {
    --navy: #27287a;
    --sky: #2ba3dc;
    --amber: #f4b547;
    --paper: #ffffff;
    --ink-soft: #3b3b55;
    --backdrop: #e9e9ec;
  }
  * { margin: 0; padding: 0; box-sizing: border-box; }
  html, body {
    width: 1200px; height: 1186px; overflow: hidden;
    background: var(--backdrop);
    font-family: "Montserrat", sans-serif;
  }
  .sheet {
    width: 1200px; height: 1186px;
    display: flex; flex-direction: column; align-items: center; justify-content: center;
    gap: 60px;
  }
  .card {
    position: relative;
    width: 900px; height: 514px;
    border-radius: 28px;
    overflow: hidden;
    box-shadow: 0 10px 30px rgba(0,0,0,.12);
  }

  /* Front */
  .card-front { background: var(--amber); }
  .front-brand {
    position: absolute; left: 0; right: 0; top: 0; bottom: 0;
    display: flex; align-items: center; justify-content: center; gap: 26px;
  }
  .brand-dot {
    width: 74px; height: 74px; border-radius: 50%;
    background: var(--navy);
  }
  .front-brand .brand-name {
    font-weight: 800; font-size: 64px; letter-spacing: 1px;
    color: var(--navy);
  }

  /* Back */
  .card-back { background: var(--paper); }
  .back-brand {
    position: absolute; left: 70px; top: 70px;
    display: flex; align-items: center; gap: 18px;
  }
  .back-brand .brand-dot { width: 52px; height: 52px; }
  .back-brand .brand-name {
    font-weight: 800; font-size: 40px; letter-spacing: .5px;
    color: var(--navy);
  }
  .divider {
    position: absolute; left: 70px; right: 70px; top: 322px;
    height: 3px;
    background: linear-gradient(to right,
      var(--sky) 0 38%, var(--navy) 38% 68%, var(--amber) 68% 100%);
  }
  .person {
    position: absolute; left: 70px; top: 246px;
  }
  .person-name {
    font-weight: 800; font-size: 34px; color: var(--navy); line-height: 1.1;
  }
  .person-title {
    font-weight: 500; font-size: 19px; color: var(--ink-soft); margin-top: 4px;
  }
  .address {
    position: absolute; right: 70px; top: 252px;
    text-align: right;
    font-weight: 500; font-size: 19px; line-height: 1.35; color: var(--ink-soft);
  }
  .contacts {
    position: absolute; left: 70px; top: 352px;
    list-style: none;
  }
  .contacts li {
    display: flex; align-items: center; gap: 14px;
    font-weight: 500; font-size: 21px; color: var(--ink-soft);
    height: 38px;
  }
  .contacts svg { width: 20px; height: 20px; flex: none; }
</style>
</head>
<body>
<main class="sheet">

  <section class="card card-front" aria-label="Card front">
    <div class="front-brand">
      <span class="brand-dot"></span>
      <span class="brand-name">CREWLINE HEALTH</span>
    </div>
  </section>

  <section class="card card-back" aria-label="Card back">
    <div class="back-brand">
      <span class="brand-dot"></span>
      <span class="brand-name">CREWLINE HEALTH</span>
    </div>

    <div class="person">
      <p class="person-name">Daniel Reyes</p>
      <p class="person-title">CEO &amp; Founder</p>
    </div>

    <address class="address" style="font-style:normal">
      410 Harbor View Rd, #112<br>
      Portsmouth, VA 23704
    </address>

    <div class="divider"></div>

    <ul class="contacts">
      <li>
        <svg viewBox="0 0 24 24" aria-hidden="true"><path fill="#2ba3dc" d="M6.6 10.8a15.1 15.1 0 0 0 6.6 6.6l2.2-2.2a1 1 0 0 1 1-.25 11.4 11.4 0 0 0 3.6.57 1 1 0 0 1 1 1V20a1 1 0 0 1-1 1A17 17 0 0 1 3 4a1 1 0 0 1 1-1h3.5a1 1 0 0 1 1 1c0 1.25.2 2.45.57 3.57a1 1 0 0 1-.25 1z"/></svg>
        800-555-0142
      </li>
      <li>
        <svg viewBox="0 0 24 24" aria-hidden="true"><rect x="2" y="5" width="20" height="14" rx="2" fill="#2ba3dc"/><path d="M3 6l9 7 9-7" fill="none" stroke="#fff" stroke-width="1.8"/></svg>
        info@crewlinehealth.com
      </li>
      <li>
        <svg viewBox="0 0 24 24" aria-hidden="true"><circle cx="12" cy="12" r="10" fill="#2ba3dc"/><path d="M2 12h20M12 2c3 3 3 17 0 20M12 2c-3 3-3 17 0 20" fill="none" stroke="#fff" stroke-width="1.4"/></svg>
        www.crewlinehealth.com
      </li>
    </ul>
  </section>

</main>
</body>
</html>
```